Heron Dusk business card design

I make handmade colourful women's beaded jewellery (necklaces and earnings).
I require a business card to be designed to truly reflect my jewellery, that is, it is different and stands out.
I would like the business card to look creative, arty, gentle and feminine and fit in with the look of my website and logo (already developed).
I would like the business card to have strong use of the water reeds that are flowing in the wind (please see the banner image on my website www.herondusk.net and attached files).

Target Market(s)

Women who are fashion conscious, hip and funky. My audience like things that are a little different and stand out in a crowd.These women are aged in their 20's-40's.

Industry/Entity Type

Jewelry

Contact Information for Business Card

Please include the following items:
1) my logo: Heron Dusk
2) my name, address and phone number: Darla Fontenot, Sydney, Australia, 0498 315 270
3) my web details: www.herondusk.net, info@herondusk.net, www.facebook.com/herondusk

Font styles to use
Other font styles liked:
• Remachine Script

Requirements
Must have
• My business card must have the following:
• 1) my personal details including all my website contacts (see above).
• 2) Heron Dusk logo
• 3) Reeds flowing in the wind (see my banner image on my website www.herondusk.net or see attached files).
Nice to have
• A sunrise in the background (rising over water)
• I would prefer that the colour scheme to fit with the Heron Dusk logo, that is the colours of an early morning sunrise i.e yellows, oranges. The use of black and white is fine.
Should not have
• I do not like a commercial manufactured look with hard edges. I would like a look that is soft and reflects an artistic, creative and independent business.

```html
<!DOCTYPE html>
<html lang="en">
<head>
<meta charset="utf-8">
<title>Heron Dusk – Business Card</title>
<link rel="stylesheet" href="https://fonts.googleapis.com/css2?family=Alegreya:wght@400&family=Kalam:wght@700&display=swap">
<style>
  :root {
    --page-bg: #8e8e8e;
    --sun-yellow: #e9b70c;
    --sun-orange: #dd7a1c;
    --ink: #1c1a17;
    --paper: #f2f2f4;
    --reed-light: #d9d9db;
    --reed-mid: #a9a9ab;
    --social: #6d6d70;
  }
  html, body {
    margin: 0;
    width: 1105px;
    height: 1200px;
    overflow: hidden;
    background: var(--page-bg);
  }
  .canvas {
    position: relative;
    width: 1105px;
    height: 1200px;
  }
  .card {
    position: absolute;
    left: 179px;
    width: 746px;
    height: 426px;
    overflow: hidden;
    background: var(--paper);
  }
  .card--front { top: 120px; }
  .card--back { top: 636px; }

  .card-shape { position: absolute; inset: 0; }

  .holder-name {
    position: absolute;
    left: 46px;
    top: 38px;
    margin: 0;
    font: 700 31px/1 "Kalam", cursive;
    color: var(--ink);
  }
  .holder-role {
    position: absolute;
    left: 46px;
    top: 92px;
    margin: 0;
    font: 700 20px/1 "Kalam", cursive;
    color: var(--ink);
  }
  .holder-address {
    position: absolute;
    left: 46px;
    top: 172px;
    margin: 0;
    font: 400 19px/32px "Alegreya", serif;
    color: var(--ink);
    font-style: normal;
  }
  .contact-list {
    position: absolute;
    left: 46px;
    top: 252px;
    margin: 0;
    padding: 0;
    list-style: none;
    font: 400 19px/33px "Alegreya", serif;
    color: var(--ink);
  }
  .contact-list li { display: flex; align-items: center; }
  .contact-icon { width: 16px; height: 16px; margin-right: 18px; flex: none; }

  .brand {
    position: absolute;
    display: flex;
    flex-direction: column;
    align-items: center;
  }
  .card--front .brand { left: 437px; top: 112px; width: 240px; }
  .card--back .brand { left: 253px; top: 95px; width: 240px; }
  .brand-name {
    font: 400 38px/1 "Alegreya", serif;
    color: var(--ink);
    white-space: nowrap;
  }
  .brand-mark {
    margin-top: 12px;
    width: 150px;
    height: 150px;
    border-radius: 50%;
    background: var(--sun-orange);
  }

  .social-row {
    position: absolute;
    left: 0;
    right: 0;
    top: 362px;
    display: flex;
    justify-content: center;
    gap: 9px;
  }
  .social-dot {
    width: 28px;
    height: 28px;
    border-radius: 50%;
    background: var(--social);
  }
</style>
</head>
<body>
<main class="canvas">

  <section class="card card--front">
    <svg class="card-shape" width="746" height="426" viewBox="0 0 746 426">
      <defs>
        <linearGradient id="sunrise-band" x1="0" y1="0" x2="0" y2="1">
          <stop offset="0" stop-color="var(--sun-yellow)"/>
          <stop offset="1" stop-color="var(--sun-orange)"/>
        </linearGradient>
      </defs>
      <rect width="746" height="426" fill="url(#sunrise-band)"/>
      <circle cx="552" cy="213" r="221" fill="var(--paper)" stroke="var(--ink)" stroke-width="5"/>
      <rect x="552" y="0" width="194" height="426" fill="var(--paper)"/>
    </svg>

    <h1 class="holder-name">Maren Ashby</h1>
    <p class="holder-role">CEO/Founder</p>
    <address class="holder-address">Darla Fontenot<br>Sydney, Australia</address>

    <ul class="contact-list">
      <li>
        <svg class="contact-icon" viewBox="0 0 16 16"><path d="M3 1l3 3-1.6 2a9 9 0 0 0 5.6 5.6L12 10l3 3-2 2C7 15 1 9 1 3z" fill="var(--ink)"/></svg>
        0498 315 270
      </li>
      <li>
        <svg class="contact-icon" viewBox="0 0 16 16"><rect x="1" y="1" width="14" height="14" fill="var(--ink)"/></svg>
        herondusk
      </li>
      <li>
        <svg class="contact-icon" viewBox="0 0 16 16"><rect x="1" y="3.5" width="14" height="10" fill="var(--ink)"/><path d="M1.5 4l6.5 5 6.5-5" fill="none" stroke="var(--paper)" stroke-width="1.3"/></svg>
        info@herondusk.net
      </li>
      <li>
        <svg class="contact-icon" viewBox="0 0 16 16"><circle cx="8" cy="8" r="7" fill="var(--ink)"/><path d="M1 8h14M8 1c-3 3.5-3 10.5 0 14M8 1c3 3.5 3 10.5 0 14" fill="none" stroke="var(--sun-orange)" stroke-width="1"/></svg>
        www.herondusk.net
      </li>
    </ul>

    <div class="brand">
      <span class="brand-name">Heron Dusk</span>
      <span class="brand-mark"></span>
    </div>
  </section>

  <section class="card card--back">
    <svg class="card-shape" width="746" height="426" viewBox="0 0 746 426" role="img" aria-label="Grey silhouettes of water reeds and bulrushes swaying in the wind">
      <defs>
        <linearGradient id="reed-field" x1="0" y1="0" x2="0" y2="1">
          <stop offset="0" stop-color="var(--paper)"/>
          <stop offset="0.45" stop-color="var(--reed-light)"/>
          <stop offset="1" stop-color="var(--reed-mid)"/>
        </linearGradient>
      </defs>
      <rect width="746" height="426" fill="url(#reed-field)"/>
    </svg>

    <div class="brand">
      <span class="brand-name">Heron Dusk</span>
      <span class="brand-mark"></span>
    </div>

    <div class="social-row">
      <span class="social-dot"></span>
      <span class="social-dot"></span>
      <span class="social-dot"></span>
      <span class="social-dot"></span>
    </div>
  </section>

</main>
</body>
</html>
```